Shopping center investment profile

We need to design a two-page 8.5" x 11" brochure that can be used as a template for profiling our shopping centers and demonstrating our track record to investors.

Our company (QLM Real Estate Investments) owns retail shopping centers in the southwestern United States. Our website is www.qlmvx.example, but we will be redesigning and modernizing the website and logo in the near future, so please do not use the color schemes or framework of the website for the brochure.

Our investors are institutional and high net worth investors who typically have an existing relationship with our company. They are determining whether to invest multi-millions of dollars in a shopping center opportunity, so the brochure needs to be professional, very high quality and provide key information about the specific property.
Updates

Additional guidance on color scheme:

We would like to see a Blue (something like Hex #5A61BC) and Gold (Hex #EDB215) or (Hex #DDA24B) color scheme with some Black accents 

Thank you!

Target Market(s)

Our target audiences are institutional investors, high net-worth individuals, financial firms and medium to large commercial real estate companies.

Industry/Entity Type

Investment

Requirements
Must have
• Clean and modern look with corresponding fonts and colors.
• Incorporates the information found in the attached "Harborline Commons profile" Pages or PDF file.
• Final file design files that can be modified easily
Nice to have
• Two examples of industry brochures are attached. These are examples of the professional quality that we are looking for, not necessarily the design or format.

```html
<!DOCTYPE html>
<html lang="en">
<head>
<meta charset="utf-8">
<title>Harborline Commons – Property Profile</title>
<link href="https://fonts.googleapis.com/css2?family=Montserrat:wght@300;400;600;700&family=Carlito:wght@400;700&display=swap" rel="stylesheet">
<style>
  :root {
    --stage: #9b9b9b;
    --paper: #ffffff;
    --blue: #545a91;
    --gold: #e0a546;
    --ink: #121217;
    --text-light: #e6e6ea;
    --text-dark: #1a1a1a;
    --sky-top: #8fa8c4;
    --sky-mid: #c9d3dd;
    --building: #8a5a3c;
  }
  * { margin: 0; padding: 0; box-sizing: border-box; }
  html, body { width: 1200px; height: 977px; overflow: hidden; background: var(--stage); }
  body { position: relative; font-family: "Carlito", "Calibri", sans-serif; }

  .brochure {
    position: absolute; left: 260px; top: 48px;
    width: 680px; height: 880px;
    background: var(--paper); overflow: hidden;
    box-shadow: 0 6px 24px rgba(0,0,0,.25);
  }
  .abs { position: absolute; }

  .hero-photo {
    left: 0; top: 136px; width: 680px; height: 382px;
    background: linear-gradient(180deg, var(--sky-top) 0%, var(--sky-mid) 45%, #b69478 70%, var(--building) 100%);
  }
  .shapes { left: 0; top: 0; width: 680px; height: 880px; }

  .title-block {
    left: 32px; top: 0; width: 266px; height: 130px;
    color: #fff; font-family: "Montserrat", sans-serif; font-weight: 700;
    font-size: 28px; line-height: 40px; text-align: right;
    padding: 22px 0 0 0; letter-spacing: .3px;
  }
  .profile-title {
    left: 330px; top: 12px; font-family: "Montserrat", sans-serif; font-weight: 300;
    font-size: 30px; color: var(--blue); letter-spacing: .5px;
  }
  .profile-bar { left: 330px; top: 62px; width: 276px; height: 23px; background: var(--gold); }
  .location {
    left: 330px; top: 97px; font-family: "Montserrat", sans-serif; font-weight: 400;
    font-size: 11px; line-height: 15px; color: #7d81a8; letter-spacing: .4px;
  }

  .facts { left: 18px; top: 433px; width: 330px; color: var(--text-light); }
  .facts h2 {
    font-family: "Montserrat", sans-serif; font-weight: 300; font-size: 19px;
    letter-spacing: .6px; color: #f2f2f4; line-height: 24px;
  }
  .facts .rule { height: 1px; background: #8d8d95; margin: 3px 0 0; width: 290px; }
  .summary-list { margin-top: 2px; font-size: 12.8px; line-height: 15.6px; }
  .summary-list .row { display: flex; }
  .summary-list .label { width: 143px; }
  .summary-list .colon { width: 19px; }
  .summary-list .strong { font-weight: 700; }
  .money-list { font-size: 11.3px; line-height: 13.4px; margin-top: 3px; }
  .money-list .row { display: flex; }
  .money-list .label { width: 155px; }
  .block { margin-top: 14px; }
  .bullets { list-style: none; font-size: 11.3px; line-height: 14px; margin-top: 3px; }
  .bullets li::before { content: "• "; }

  .highlights { left: 360px; top: 356px; width: 276px; color: var(--text-dark); }
  .highlights h2 {
    font-family: "Montserrat", sans-serif; font-weight: 700; font-size: 24px;
    text-align: right; letter-spacing: .6px; color: #111;
  }
  .highlights ul { list-style: none; font-size: 10.4px; line-height: 13.3px; margin-top: 4px; }
  .highlights li { padding-left: 8px; text-indent: -8px; }
  .highlights li::before { content: "• "; }
  .highlights .results { margin-top: 16px; }

  .footer-band { left: 0; top: 823px; width: 680px; height: 57px; background: var(--gold); }
  .tagline {
    left: 19px; top: 841px; font-family: "Montserrat", sans-serif; font-weight: 600;
    font-size: 15px; color: #fff; letter-spacing: .8px;
  }
  .brand-dot {
    left: 262px; top: 838px; width: 14px; height: 14px; border-radius: 50%; background: #fff;
  }
  .brand-name {
    left: 282px; top: 834px; width: 92px; font-size: 11.5px; line-height: 13.5px;
    font-weight: 400; color: var(--ink);
  }
  .office {
    left: 384px; top: 830px; font-size: 11.5px; line-height: 13.5px; color: var(--ink); font-style: normal;
  }
  .divider { left: 518px; top: 832px; width: 1px; height: 40px; background: var(--ink); }
  .contact {
    left: 526px; top: 836px; font-size: 11.5px; line-height: 14px; color: var(--ink);
  }
  .contact .row { display: flex; }
  .contact .label { width: 48px; }
</style>
</head>
<body>
  <main class="brochure">
    <div class="abs hero-photo" role="img" aria-label="Photograph of the shopping center storefronts with arched walkways under a cloudy sky"></div>

    <svg class="abs shapes" width="680" height="880" viewBox="0 0 680 880" aria-hidden="true">
      <polygon points="32,0 292,0 322,130 32,130" fill="var(--blue)"/>
      <polygon points="0,335 360,485 680,470 680,823 0,823" fill="var(--ink)"/>
      <path d="M349,415 Q349,345 419,345 L646,345 L646,776 L349,776 Z" fill="var(--gold)"/>
    </svg>

    <h1 class="abs title-block">Harborline<br>Commons</h1>
    <p class="abs profile-title">Property Profile</p>
    <div class="abs profile-bar"></div>
    <p class="abs location">SWC OF HARBORLINE RD AND MERIDIAN RD<br>ALDER SPRINGS, ARIZONA</p>

    <section class="abs facts">
      <h2>SUMMARY</h2>
      <div class="summary-list">
        <div class="row"><span class="label">Property Type</span><span class="colon">:</span><span class="strong">Shopping Center</span></div>
        <div class="row"><span class="label">Size</span><span class="colon">:</span><span>79,490 sq ft</span></div>
        <div class="row"><span class="label">Purchased</span><span class="colon">:</span><span>April 2011</span></div>
        <div class="row"><span class="label">Total Investment</span><span class="colon">:</span><span>$X,XXX,XXX</span></div>
        <div class="row"><span class="label">Purchase Occupancy</span><span class="colon">:</span><span>8.39%</span></div>
        <div class="row"><span class="label">Current Occupancy</span><span class="colon">:</span><span>97.29%</span></div>
        <div class="row"><span>Projected 5-year IRR (Unleveraged) XX.XX%</span></div>
      </div>

      <div class="block">
        <h2>INVESTMENT INFORMATION</h2>
        <div class="rule"></div>
        <div class="money-list">
          <div class="row"><span class="label">Purchase Price</span><span>$X,XXX,XXX</span></div>
          <div class="row"><span class="label">Sponsor Acquisition Fee</span><span>$XX,XXX</span></div>
          <div class="row"><span class="label">Painting and Landscape</span><span>$XXX,XXX</span></div>
          <div class="row"><span class="label">TI/LC Reserve</span><span>$X,XXX,XXX</span></div>
          <div class="row"><span class="label">Operating Expenses</span><span>$XXX,XXX</span></div>
        </div>
      </div>

      <div class="block">
        <h2>TOTAL CASH INVESTMENT</h2>
        <div class="rule"></div>
        <div class="money-list"><div class="row"><span class="label">Investor / Sponsor Split</span><span>XX% / XX%</span></div></div>
      </div>

      <div class="block">
        <h2>STRUCTURE</h2>
        <ul class="bullets">
          <li>Cash Flow Pari Passu</li>
          <li>Acquisition Fee</li>
          <li>Management Fee</li>
        </ul>
      </div>
    </section>

    <section class="abs highlights">
      <h2>OPPORTUNITY</h2>
      <ul>
        <li>Bank owned property with attractive purchase price</li>
        <li>Strong relationship with seller’s broker and decision makers</li>
        <li>Redevelopment upside with management and leasing</li>
        <li>No major renovations required</li>
        <li>Alder Springs location has very strong population, education and income demographics</li>
        <li>Adjacent to premier 2,500-residence master planned community of Copperleaf Lakes</li>
        <li>Strong employment area with the new Northgate Regional hospital and the adjacent Westfield Cancer Center</li>
      </ul>
      <h2 class="results">RESULTS</h2>
      <ul>
        <li>Stabilized the shopping center within three years, producing excellent results for investors</li>
        <li>Transformed the center into a vibrant destination that the surrounding community is excited about</li>
        <li>Transitioned legacy tenants to upgrade the business operators</li>
        <li>Reduced the shopping center’s operating expenses by replacing vendors and appealing property taxes</li>
      </ul>
    </section>

    <div class="abs footer-band"></div>
    <p class="abs tagline">ONE PROPERTY AT A TIME</p>
    <div class="abs brand-dot" aria-hidden="true"></div>
    <p class="abs brand-name">QLM Real Estate Investments</p>
    <address class="abs office">4410 East Palo Verde<br>Suite 200<br>Sunmesa, Arizona 85000</address>
    <div class="abs divider"></div>
    <div class="abs contact">
      <div class="row"><span class="label">Phone</span><span>: 555-014-2900</span></div>
      <div class="row"><span class="label">Web</span><span>: www.qlmvx.example</span></div>
    </div>
  </main>
</body>
</html>
```